Willow Creek Gatherings Event Planning in need of a design!!

Event Planning company, does a variety of events. I like simple more rustic designs focused on almond blossoms. We are based out of Northern California, the heart of almond country. I would like to see colors in light pinks, beige, light browns, whites or creams. the final design should communicate rustic simplicity. Below are some pictures of Almond blossoms and design ideas I prefer the one called Tulip Grove. Thanks

Target Market(s)

Women in the mid twenties and older. They should be in the upper middle class in need of an amazing party design and coordinator

Industry/Entity Type

Event Planning

Contact Information for Business Card

Maren Lockwood 530-624-0295almondbaffairs@gmail.comalmondblossomaffairs.com

Font styles to use
Other font styles liked:
• Amatic SC

Requirements
Must have
• almond blossom
• my information
• simplicity
Nice to have
• rustic design
• vintage feel
• whimsical
Should not have
• i like pink but not over the top

```html
<!DOCTYPE html>
<html lang="en">
<head>
<meta charset="utf-8">
<title>Willow Creek Gatherings – Business Card</title>
<link href="https://fonts.googleapis.com/css2?family=Open+Sans:wght@400;600&display=swap" rel="stylesheet">
<style>
  :root {
    --backdrop: #e6e4e1;
    --card-dark: #121212;
    --card-dark-edge: #1d1d1d;
    --blossom-pink: #ec8fbf;
    --text-light: #f2f2f2;
    --rule: #3a3a3a;
    --orchard-grey: #8f8a83;
    --orchard-green: #5d7a45;
    --orchard-shade: #4a4643;
  }
  * { box-sizing: border-box; margin: 0; padding: 0; }
  html, body {
    width: 1200px; height: 900px; overflow: hidden;
    background: var(--backdrop);
    font-family: "Open Sans", Arial, sans-serif;
  }
  .sheet {
    width: 1200px; height: 900px;
    display: flex; flex-direction: column;
    align-items: center; justify-content: center; gap: 36px;
  }
  .card {
    position: relative;
    width: 700px; height: 400px;
    overflow: hidden;
    box-shadow: 0 6px 18px rgba(0,0,0,0.18);
  }

  /* Front: orchard photograph with brand name */
  .card-front .orchard-photo {
    position: absolute; inset: 0;
    background:
      linear-gradient(100deg, rgba(93,122,69,0.85) 0%, rgba(93,122,69,0) 28%),
      linear-gradient(180deg, var(--orchard-shade) 0%, var(--orchard-grey) 55%, #b0aaa2 100%);
  }
  .card-front .brand-name {
    position: absolute; left: 70px; top: 150px;
    color: #ffffff;
    font-size: 40px; font-weight: 400; letter-spacing: 2px;
    line-height: 1.15;
  }

  /* Back: contact side */
  .card-back {
    background: radial-gradient(ellipse at 40% 30%, var(--card-dark-edge) 0%, var(--card-dark) 70%);
  }
  .card-back .holder-name {
    position: absolute; left: 58px; top: 150px;
    color: var(--blossom-pink);
    font-size: 22px; font-weight: 600;
  }
  .card-back .brand-name {
    position: absolute; right: 50px; top: 80px;
    color: var(--blossom-pink);
    font-size: 34px; font-weight: 400; letter-spacing: 1.5px;
    text-align: right; line-height: 1.15;
  }
  .card-back .divider {
    position: absolute; left: 270px; right: 50px; top: 205px;
    height: 1px; background: var(--rule);
  }
  .contact-list {
    position: absolute; right: 50px; top: 275px;
    list-style: none;
  }
  .contact-list li {
    display: flex; justify-content: flex-end; align-items: center; gap: 14px;
    color: var(--text-light);
    font-size: 18px; line-height: 28px;
  }
  .contact-list svg { width: 14px; height: 14px; fill: var(--blossom-pink); }
</style>
</head>
<body>
<main class="sheet">
  <section class="card card-front">
    <div class="orchard-photo" role="img" aria-label="Photograph of an orchard lane lined with blossoming almond trees"></div>
    <div class="brand-name">WILLOW CREEK<br>GATHERINGS</div>
  </section>

  <section class="card card-back">
    <div class="holder-name">Maren Lockwood</div>
    <div class="brand-name">WILLOW CREEK<br>GATHERINGS</div>
    <div class="divider"></div>
    <ul class="contact-list">
      <li>530-817-4362
        <svg viewBox="0 0 16 16" aria-hidden="true"><path d="M3.6 1.2l2.4 2.9-1.4 1.6c.9 2 2.4 3.5 4.4 4.4l1.6-1.4 2.9 2.4-1.5 2.2C7 13.8 2.2 9 .9 3.7z"/></svg>
      </li>
      <li>willowcgather@mailbox.test
        <svg viewBox="0 0 16 16" aria-hidden="true"><path d="M1 3h14v10H1z M2 4v.5l6 4 6-4V4z" fill-rule="evenodd"/></svg>
      </li>
      <li>willowcreekgatherings.test
        <svg viewBox="0 0 16 16" aria-hidden="true"><circle cx="8" cy="8" r="7"/><path d="M1 8h14M8 1c3 3 3 11 0 14M8 1c-3 3-3 11 0 14" stroke="#121212" stroke-width="1.2" fill="none"/></svg>
      </li>
    </ul>
  </section>
</main>
</body>
</html>
```